Summit Bodyform Gym Website

We need a website design for our gym.

Summit is the UAE's first calisthenics and parkour gym. The theme under which the gym revolves is that one does not require any machinery to workout as our bodies could be themselves the machinery. The gym is designed to be the more of a social hub rather than an "in-and-out" gym, where people come train, have fun, hang out and socialize for a few hours rather than just train for 60 minutes then leave. The gym is designed to be a big open space with lots of natural sunlight, natural wood and plants all over the place to create a natural and refreshing setting. We also use recycled material throughout the gym and recycle our waste as being green is part of our philosophy. We currently also have some of the world's top and most recognized calisthenics athletes working with us.

We would like our website to reflect all that as well as provide a simple, interactive and fun way for visitors to be able to get class and gym information, check out gym media and contact us for bookings.

Target Market(s)

Ages 15-35

Industry/Entity Type

Fitness

Coding

Coded - Design and coding required

Number of Pages Required

4 page

Font styles to use
Decorative

Colors
0792cd

Requirements
Must have
• Class descriptions
• Gym description
• Class schedules
• Trainer profiles
• Gym philosophy
• Contact Details
Nice to have
• A link to contact us directly for a free first trial class

```html
<!DOCTYPE html>
<html lang="en">
<head>
<meta charset="utf-8">
<title>Summit Bodyform Gym</title>
<link rel="stylesheet" href="https://fonts.googleapis.com/css2?family=Roboto:ital,wght@0,300;0,400;0,500;0,700;1,400&family=Roboto+Condensed:wght@400;500&display=swap">
<style>
:root{
  --brand:#0fb0d0;
  --brand-dark:#0a9dbd;
  --ink:#3a3a3a;
  --muted:#8a8a8a;
  --soft-bg:#f8f8f8;
  --line:#e6e6e6;
  --footer:#2e2e2e;
  --footer-text:#a9a9a9;
  --white:#ffffff;
}
*{box-sizing:border-box;margin:0;padding:0}
html,body{width:1200px;height:2612px;overflow:hidden}
body{font-family:"Roboto",Arial,sans-serif;color:var(--ink);background:var(--white);position:relative}
h1,h2{font-weight:400}
.abs{position:absolute}

/* top bar */
.topbar{left:0;top:0;width:1200px;height:56px;background:var(--brand)}
.topbar-text{left:127px;top:19px;font-size:13px;color:var(--white);font-weight:500}
.topbar-social{right:127px;top:10px;display:flex;gap:10px}
.topbar-social span{width:35px;height:35px;border:1.5px solid var(--white);border-radius:50%;display:block}

/* header */
.header{left:0;top:56px;width:1200px;height:104px;background:var(--white)}
.logo{left:127px;top:88px;display:flex;align-items:center;gap:8px}
.logo-name{font-size:30px;font-weight:700;color:#2b2b2b;line-height:1}
.logo-dot{width:14px;height:14px;border-radius:50%;background:var(--brand)}
.nav{left:310px;top:98px;display:flex;gap:28px;font-size:14.5px;color:#555}
.nav .active{color:var(--brand)}

/* hero */
.hero{left:0;top:160px;width:1200px;height:523px;background:radial-gradient(ellipse at 75% 45%,#5a4b40 0%,#2c2824 35%,#141414 70%,#0b0b0b 100%)}
.hero-title{left:113px;top:312px;font-family:"Roboto Condensed",Arial,sans-serif;font-size:47px;font-weight:400;color:var(--white)}
.hero-title em{font-style:normal;color:var(--brand)}
.hero-text{left:118px;top:393px;width:530px;font-size:14.5px;line-height:26px;color:#e6e6e6}
.hero-btn{left:118px;top:503px;width:147px;height:44px;background:var(--brand);border-radius:4px;color:var(--white);font-size:14px;font-weight:500;display:flex;align-items:center;justify-content:center}
.hero-arrows{left:1112px;top:600px}

/* about */
.about-photo{left:127px;top:739px;width:430px;height:256px;background:linear-gradient(180deg,#a36b3f 0%,#6d7d3d 35%,#b08559 60%,#3a3a3a 100%)}
.about-title{left:590px;top:735px;font-size:21px;color:#444}
.about-text{left:593px;top:775px;width:476px;font-size:11.8px;line-height:21.5px;color:#777;text-align:justify}
.about-text p+p{margin-top:13px}
.about-more{left:595px;top:977px;font-size:12px;color:var(--brand)}

/* programs */
.programs{left:0;top:1045px;width:1200px;height:680px;background:var(--soft-bg);border-top:1px solid var(--line)}
.section-title{width:1200px;left:0;text-align:center;font-size:23px;color:#333}
.card{width:283px}
.card-photo{height:159px}
.card-name{margin-top:12px;text-align:center;font-size:20px;color:#444}
.card-text{margin-top:6px;text-align:center;font-size:11.5px;line-height:19px;color:#888}

/* testimonials */
.testimonials{left:0;top:1725px;width:1200px;height:304px;background:linear-gradient(180deg,#0db4d3,#08a6c6)}
.quote-text{left:290px;top:1806px;width:620px;text-align:center;font-size:12px;line-height:21.5px;color:var(--white)}
.quote-mark{font-size:28px;color:var(--white);font-family:Georgia,serif}
.quote-close{font-size:20px;font-family:Georgia,serif;line-height:0;vertical-align:-4px;margin-left:8px}
.avatar{left:514px;top:1893px;width:84px;height:84px;border-radius:50%;border:4px solid rgba(255,255,255,.6);background:linear-gradient(160deg,#dfe6ea,#9fb2bd)}
.person-name{left:617px;top:1912px;font-size:13px;color:var(--white)}
.person-role{left:617px;top:1933px;font-size:11px;font-style:italic;color:var(--white)}

/* trial cta */
.cta-title{top:2074px}
.cta-text{left:200px;top:2125px;width:800px;text-align:center;font-size:14.5px;line-height:26px;color:#777}
.cta-form{left:287px;top:2198px;width:624px;height:49px;display:flex}
.cta-input{flex:0 0 386px;border:1px solid #d8d8d8;border-right:none;border-radius:25px 0 0 25px;padding-left:24px;display:flex;align-items:center;font-size:13px;color:#888}
.cta-btn{flex:1;background:var(--brand);border-radius:0 25px 25px 0;color:var(--white);font-size:14.5px;font-weight:500;display:flex;align-items:center;justify-content:center;gap:12px}

/* footer */
.footer{left:0;top:2305px;width:1200px;height:307px;background:var(--footer)}
.f-head{font-size:16px;color:#eee}
.f-links{list-style:none;font-size:11.5px;line-height:24.5px;color:var(--footer-text)}
.blog-item{display:flex;gap:10px;width:260px}
.blog-icon{width:20px;height:15px;border:1.5px solid #bbb;border-radius:2px;margin-top:3px;flex:none}
.blog-date{font-size:11.5px;color:#ddd}
.blog-text{font-size:11px;line-height:19px;color:var(--footer-text)}
.news-text{left:606px;top:2382px;width:230px;font-size:11.5px;line-height:20px;color:var(--footer-text)}
.news-input{left:608px;top:2438px;width:211px;height:36px;background:var(--white);font-size:9.5px;color:#aaa;padding:13px 0 0 12px}
.news-btn{left:608px;top:2486px;width:107px;height:35px;background:var(--brand);color:var(--white);font-size:11px;font-weight:500;display:flex;align-items:center;justify-content:center}
.f-logo{left:890px;top:2345px;display:flex;align-items:center;gap:10px}
.f-logo-name{font-size:44px;font-weight:700;color:#6a6a6a}
.f-logo-dot{width:24px;height:24px;border-radius:50%;background:var(--brand)}
.f-social{left:893px;top:2508px;display:flex;gap:6px}
.f-social span{width:24px;height:24px;border-radius:50%;display:block}
.copyright{left:125px;top:2561px;font-size:11.5px;color:var(--footer-text)}
</style>
</head>
<body>

<div class="abs topbar"></div>
<div class="abs topbar-text">Summit is the UAE's first calisthenics and parkour gym.</div>
<div class="abs topbar-social"><span></span><span></span><span></span><span></span><span></span></div>

<header class="abs header"></header>
<div class="abs logo"><span class="logo-dot"></span><span class="logo-name">Summit</span></div>
<nav class="abs nav">
  <span class="active">Home</span><span>Class descriptions</span><span>Gym description</span><span>Class schedules</span><span>Trainer profiles</span><span>Gym philosophy</span><span>Contact</span>
</nav>

<section class="abs hero" role="img" aria-label="Athlete doing a push-up on a dark gym floor"></section>
<h1 class="abs hero-title">Summit <em>Bodyform Gym</em></h1>
<p class="abs hero-text">Lorem ipsum dolor sit amet, consectetur adipiscing elit, sed do eiusmod tempor incididunt ut labore et dolore magna aliqua. Ut enim ad minim veniam, quis exercitation ullamco  iut aliquip ex ea commodo.</p>
<div class="abs hero-btn">LEARN MORE</div>
<svg class="abs hero-arrows" width="44" height="32" viewBox="0 0 44 32"><path d="M14 2 L2 16 L14 30 M30 2 L42 16 L30 30" fill="none" stroke="#dcdcdc" stroke-width="2"/></svg>

<div class="abs about-photo" role="img" aria-label="Plant-covered gym sign above a dumbbell rack on a wooden wall"></div>
<h2 class="abs about-title">About Summit Bodyform Gym</h2>
<div class="abs about-text">
  <p>Lorem ipsum dolor sit amet, consectetur adipiscing elit, sed do eiusmod tempor incididunt ut labore et dolore magna aliqua. Ut enim ad minim veniam, quis nostrud exercitation ullamco laboris nisi ut aliquip ex ea commodo consequat. Duis aute irure dolor in reprehenderit in voluptate velit esse cillum dolore eu fugiat nulla pariatur. Excepteur sint occaecat cupidatat non proident, sunt in culpa .</p>
  <p>Lorem ipsum dolor sit amet, consectetur adipiscing elit, sed do eiusmod tempor incididunt ut labore et dolore magna aliqua. Ut enim ad minim veniam, quis nostrud exercitation ullamco laboris nisi ut aliquip ex ea commodo consequat.</p>
</div>
<div class="abs about-more">Read More &gt;</div>

<section class="abs programs"></section>
<h2 class="abs section-title" style="top:1090px">Our Programs</h2>

<div class="abs card" style="left:127px;top:1146px"><div class="card-photo" role="img" aria-label="Gym floor with dumbbells and plant wall" style="background:linear-gradient(180deg,#a57446,#8a5a3a 50%,#a33b36)"></div><div class="card-name">Summit</div><div class="card-text">Lorem ipsum dolor sit amet, consectetur adipiscing elit<br>sed do eiusmod tempor incididunt ut</div></div>
<div class="abs card" style="left:456px;top:1146px"><div class="card-photo" role="img" aria-label="Calisthenics rig in a bright training hall" style="background:linear-gradient(180deg,#d9dcdc,#a9aca8 60%,#6f7370)"></div><div class="card-name">Summit</div><div class="card-text">Lorem ipsum dolor sit amet, consectetur adipiscing elit<br>sed do eiusmod tempor incididunt ut</div></div>
<div class="abs card" style="left:784px;top:1146px"><div class="card-photo" role="img" aria-label="Studio floor with blue mats" style="background:linear-gradient(180deg,#6d7f8c,#8b5a4a 60%,#a0503d)"></div><div class="card-name">Summit</div><div class="card-text">Lorem ipsum dolor sit amet, consectetur adipiscing elit<br>sed do eiusmod tempor incididunt ut</div></div>
<div class="abs card" style="left:127px;top:1423px"><div class="card-photo" role="img" aria-label="Wooden gymnastic ring hanging from a blue frame" style="background:linear-gradient(135deg,#2f6fa8,#1e3d5c 60%,#b08c62)"></div><div class="card-name">Summit</div><div class="card-text">Lorem ipsum dolor sit amet, consectetur adipiscing elit<br>sed do eiusmod tempor incididunt ut</div></div>
<div class="abs card" style="left:456px;top:1423px"><div class="card-photo" role="img" aria-label="Open hall with pull-up rigs" style="background:linear-gradient(180deg,#c9cdd0,#9ea3a5 60%,#7b807f)"></div><div class="card-name">Summit</div><div class="card-text">Lorem ipsum dolor sit amet, consectetur adipiscing elit<br>sed do eiusmod tempor incididunt ut</div></div>
<div class="abs card" style="left:784px;top:1423px"><div class="card-photo" role="img" aria-label="Athlete training on bars by a plant wall" style="background:linear-gradient(135deg,#2b3f6a,#5a6a48 55%,#3a2f2a)"></div><div class="card-name">Summit</div><div class="card-text">Lorem ipsum dolor sit amet, consectetur adipiscing elit<br>sed do eiusmod tempor incididunt ut</div></div>

<section class="abs testimonials"></section>
<h2 class="abs section-title" style="top:1763px;color:#fff">Testimonials</h2>
<span class="abs quote-mark" style="left:258px;top:1788px">&ldquo;</span>
<p class="abs quote-text">Lorem ipsum dolor sit amet, consectetur adipiscing elit, sed do eiusmod tempor incididunt ut labore et dolore magna aliqua. Ut enim ad minim veniam, quis nostrud exercitation ullamco laboris nisi ut aliquip ex ea commodo consequat. aute irure dolor in reprehenderit in voluptate velit esse cillum dolore eu fugiat nulla pariatur.<span class="quote-close">&rdquo;</span></p>
<div class="abs avatar" role="img" aria-label="Portrait of the client giving the testimonial"></div>
<div class="abs person-name">John Doe</div>
<div class="abs person-role">Director</div>

<h2 class="abs section-title cta-title">Get Summit Bodyform Gym Training</h2>
<p class="abs cta-text">Lorem ipsum dolor sit amet, consectetur adipiscing elit, sed do eiusmod tempor incididunt ut labore et dolore magna aliqua. Ut enim ad minim veniam, quis nostrud exercitation ullamco laboris nisi ut aliquip ex ea commodo.</p>
<div class="abs cta-form">
  <div class="cta-input">Enter your email</div>
  <div class="cta-btn">FREE FIRST TRIAL CLASS
    <svg width="18" height="18" viewBox="0 0 18 18"><circle cx="9" cy="9" r="9" fill="#fff"/><path d="M7 5 L11 9 L7 13" fill="none" stroke="#0fb0d0" stroke-width="2"/></svg>
  </div>
</div>

<footer class="abs footer"></footer>
<div class="abs f-head" style="left:125px;top:2344px">Information</div>
<ul class="abs f-links" style="left:125px;top:2380px">
  <li>Home</li><li>Descriptions</li><li>Schedules</li><li>Trainer profiles</li><li>Philosophy</li><li>Contact us</li>
</ul>
<div class="abs f-head" style="left:301px;top:2344px">Latest Blog</div>
<div class="abs blog-item" style="left:301px;top:2383px"><span class="blog-icon"></span><div><div class="blog-date">Posted On 20 Dec 2015</div><div class="blog-text">Lorem ipsum dolor sit amet, consectetur adipiscing elit eiusmod tempor</div></div></div>
<div class="abs blog-item" style="left:301px;top:2465px"><span class="blog-icon"></span><div><div class="blog-date">Posted On 20 Dec 2015</div><div class="blog-text">Lorem ipsum dolor sit amet, consectetur adipiscing elit eiusmod tempor</div></div></div>
<div class="abs f-head" style="left:605px;top:2344px">Newsletter Sign up</div>
<p class="abs news-text">Lorem ipsum dolor sit amet, consectetur adipiscing elit eiusmod tempor</p>
<div class="abs news-input">Email Address...</div>
<div class="abs news-btn">SUBSCRIBE</div>
<div class="abs f-logo"><span class="f-logo-dot"></span><span class="f-logo-name">Summit</span></div>
<div class="abs f-social">
  <span style="background:#3b5b9a"></span><span style="background:#2aa3df"></span><span style="background:#1d7bb5"></span><span style="background:#d9473b"></span><span style="background:#f0892a"></span>
</div>
<div class="abs copyright">Copyright © 2015 Summit Bodyform Gym. All rights reserved.</div>

</body>
</html>
```